Sleek wordpress site for Bramblecrest finishing works

We are a commercial job shop that serves B2B, govt & LEO and retail clients.We need a wordpress site with 6 individual pages: homepage, coating, laser engraving, laser cutting, part marking, and contact us. I have attached an outline of the desired flow and sub headings for each page. I would like to incorporate the colors of the logo through out the site to be clean and sleek enough to appeal to B2B commercial clients yet be inviting enough for retail clients.

I would like to have easy picture functionality so photographs on each page can be updated easily.

Target Market(s)

B2B industrial & Govt and Military part marking, laser engraving and coating: machine shops, aerospace companies, tool manufactures. Retail: personalized gifts, Job Shop

Coding

Coded - Design and coding required

Font styles to use
Sans Serif
Other font styles liked:
• Open to suggestion

Colors
0255a3
3176b5
eaf1f7
cfdeed
ffffff

Requirements
Must have
• Clean easy to navigate flow, separate pages as indicated on attached outline, high class feel. Great picture functionality, professional and inviting feel,
• **update: needs to be optimized for mobile, should have a gallery function. Gallery can be an additional page or embedded
Nice to have
• Social media connectivity links,
Should not have
• crappy plugins that make back-end management difficult, no blog

```html
<!DOCTYPE html>
<html lang="en">
<head>
<meta charset="utf-8">
<title>Bramblecrest finishing works</title>
<link href="https://fonts.googleapis.com/css2?family=Lato:wght@700&family=Michroma&family=Poppins:wght@300;400;500;600&display=swap" rel="stylesheet">
<style>
  :root {
    --brand: #0255a3;
    --brand-mid: #3176b5;
    --brand-pale: #eaf1f7;
    --brand-soft: #cfdeed;
    --white: #ffffff;
    --ink: #333333;
    --muted: #8d8d8d;
    --grey-disc: #efefef;
  }
  * { margin: 0; padding: 0; box-sizing: border-box; }
  html, body { width: 1200px; height: 1078px; overflow: hidden; background: var(--white); }
  body { position: relative; font-family: "Poppins", sans-serif; color: var(--ink); }

  .topbar { position: absolute; top: 0; left: 0; width: 1200px; height: 52px; background: var(--brand); }
  .topbar__item { position: absolute; top: 0; height: 48px; display: flex; align-items: center; gap: 10px; color: var(--brand-soft); font-weight: 300; }
  .topbar__phone { left: 695px; font-size: 19px; }
  .topbar__mail { left: 905px; font-size: 15px; }

  .header { position: absolute; top: 52px; left: 0; width: 1200px; height: 116px; background: var(--white); }
  .brand-name { position: absolute; left: 77px; top: 32px; color: var(--brand); font-weight: 600; font-size: 25px; line-height: 1.15; letter-spacing: .2px; }
  .nav { position: absolute; right: 79px; top: 46px; display: flex; gap: 32px; list-style: none; font-size: 14.5px; }
  .nav a { color: var(--muted); text-decoration: none; text-transform: uppercase; }
  .nav a.is-current { color: var(--brand); }

  .hero { position: absolute; top: 168px; left: 0; width: 1200px; height: 573px;
    background: radial-gradient(ellipse at 60% 45%, #3f83c2 0%, #2368ad 45%, #0d58a3 100%); }
  .hero__title { position: absolute; top: 300px; left: 0; width: 1200px; text-align: center; font-family: "Lato", sans-serif; font-weight: 700; font-size: 62px; color: var(--white); }
  .hero__text { position: absolute; top: 390px; left: 125px; width: 950px; text-align: center; color: var(--brand-pale); font-weight: 300; font-size: 19px; line-height: 25px; }
  .hero__button { position: absolute; top: 487px; left: 485px; width: 230px; height: 58px; background: var(--white); border-radius: 3px; color: var(--brand); font-size: 22px; display: flex; align-items: center; justify-content: center; text-decoration: none; }

  .service { position: absolute; top: 672px; width: 260px; text-align: center; }
  .service__disc { position: relative; width: 136px; height: 136px; margin: 0 auto; border-radius: 50%; background: var(--white); border: 2px solid var(--brand); display: flex; align-items: center; justify-content: center; }
  .service__disc::after { content: ""; position: absolute; left: -40px; top: 118px; width: 150px; height: 30px; border-radius: 50%; background: radial-gradient(ellipse at 60% 40%, rgba(0,0,0,.35), rgba(0,0,0,0) 70%); z-index: -1; }
  .service__disc--active { background: var(--grey-disc); border: 10px solid #c9c9c9; box-shadow: 0 0 0 2px #d6d6d6; }
  .service__disc--active::after { display: none; }
  .service__title { margin-top: 32px; font-family: "Michroma", sans-serif; font-size: 18.5px; letter-spacing: .5px; color: #3a3a3a; }
  .service__text { margin: 16px auto 0; width: 245px; color: var(--muted); font-size: 15px; line-height: 19px; font-weight: 300; }
  .service__link { display: inline-block; margin-top: 22px; color: #222; font-size: 16.5px; text-decoration: underline; text-underline-offset: 3px; }

  .footer { position: absolute; top: 1027px; left: 0; width: 1200px; height: 51px; background: var(--brand); display: flex; align-items: center; justify-content: center; gap: 6px; color: var(--brand-soft); font-size: 15px; font-weight: 300; }
  .footer__name { font-family: "Michroma", sans-serif; font-size: 13.5px; color: var(--white); }
</style>
</head>
<body>
  <div class="topbar">
    <div class="topbar__item topbar__phone">
      <svg width="20" height="22" viewBox="0 0 20 22"><path d="M4 1 L8 1 L9 6 L6.5 8 Q8.5 13 13 15 L15 12.5 L19 14 L19 18 Q18 21 14 20.5 Q3 17 1 5 Q1 1.5 4 1Z" fill="#ffffff"/></svg>
      <span>(555) 304-7721</span>
    </div>
    <div class="topbar__item topbar__mail">
      <svg width="20" height="14" viewBox="0 0 20 14"><rect x="0.5" y="0.5" width="19" height="13" fill="#ffffff"/><path d="M1 1 L10 8 L19 1" fill="none" stroke="#0255a3" stroke-width="1.4"/></svg>
      <span>hello@bramblecrestworks.com</span>
    </div>
  </div>

  <header class="header">
    <div class="brand-name">Bramblecrest<br>finishing works</div>
    <ul class="nav">
      <li><a class="is-current" href="#">Home</a></li>
      <li><a href="#">Coating</a></li>
      <li><a href="#">Laser Engraving</a></li>
      <li><a href="#">Laser Cutting</a></li>
      <li><a href="#">Part Marketing</a></li>
      <li><a href="#">Contact Us</a></li>
    </ul>
  </header>

  <section class="hero" role="img" aria-label="Blue-tinted photograph of machined metal parts laid on a carbon fibre surface"></section>
  <h1 class="hero__title">PART MARKETING</h1>
  <p class="hero__text">Marketing is a big picture perspective. It is the systematic planning, implementation and control of a mix of business activities intended to bring together buyers and sellers for the exchange or transfer of products. Advertising is part of the overall promotion efforts of the company.</p>
  <a class="hero__button" href="#">LEARN MORE</a>

  <div class="service" style="left:71px">
    <div class="service__disc service__disc--active">
      <svg width="80" height="60" viewBox="0 0 80 60"><path d="M46 40 L52 22 L70 4 Q74 2 77 6 Q78 9 76 11 L58 29 Z" fill="none" stroke="#0255a3" stroke-width="3" stroke-linejoin="round"/><path d="M52 22 L58 29 M66 8 L73 15" stroke="#0255a3" stroke-width="3"/><line x1="22" y1="45" x2="46" y2="45" stroke="#0255a3" stroke-width="2"/></svg>
    </div>
    <h2 class="service__title">PART MARKETING</h2>
    <p class="service__text">Ceravella is a spray on ceramic based finish that can be applied to metals, plastics...</p>
    <a class="service__link" href="#">LEARN MORE</a>
  </div>

  <div class="service" style="left:341px">
    <div class="service__disc">
      <svg width="60" height="136" viewBox="0 0 60 136"><line x1="30" y1="0" x2="30" y2="70" stroke="#c4c4c4" stroke-width="3"/><g stroke="#c4c4c4" stroke-width="3" stroke-linecap="round"><line x1="30" y1="62" x2="30" y2="84"/><line x1="18" y1="62" x2="24" y2="66"/><line x1="42" y1="62" x2="36" y2="66"/><line x1="14" y1="72" x2="22" y2="72"/><line x1="38" y1="72" x2="46" y2="72"/><line x1="18" y1="82" x2="24" y2="78"/><line x1="42" y1="82" x2="36" y2="78"/></g></svg>
    </div>
    <h2 class="service__title">COATING</h2>
    <p class="service__text">Ceravella is a spray on ceramic based finish that can be applied to metals, plastics...</p>
    <a class="service__link" href="#">LEARN MORE</a>
  </div>

  <div class="service" style="left:605px">
    <div class="service__disc">
      <svg width="44" height="64" viewBox="0 0 44 64"><g fill="none" stroke="#c4c4c4" stroke-width="2.5"><rect x="13" y="2" width="18" height="8"/><path d="M11 10 H33 L30 30 L22 38 L14 30 Z"/><line x1="22" y1="38" x2="22" y2="56"/><line x1="4" y1="60" x2="40" y2="60"/></g></svg>
    </div>
    <h2 class="service__title">LASER ENGRAVING</h2>
    <p class="service__text">With our selection of CO2 and fiber lasers there are very few materials and substrates...</p>
    <a class="service__link" href="#">LEARN MORE</a>
  </div>

  <div class="service" style="left:873px">
    <div class="service__disc">
      <svg width="56" height="56" viewBox="0 0 56 56"><g fill="none" stroke="#c4c4c4" stroke-width="3" stroke-linejoin="round"><rect x="6" y="22" width="46" height="14" transform="rotate(-45 29 29)"/><path d="M12 40 L34 12 L42 16 L20 46 L10 50 Z"/></g></svg>
    </div>
    <h2 class="service__title">LASER CUTTING</h2>
    <p class="service__text">We can custom cut virtually any shape or design in a variety of substrates or materials.</p>
    <a class="service__link" href="#">LEARN MORE</a>
  </div>

  <footer class="footer">
    <span style="font-size:21px;color:#fff">&copy;</span>
    <span class="footer__name">Bramblecrest finishing works - 2018.</span>
    <span>All Rights Reserved.</span>
  </footer>
</body>
</html>
```